Modern business card design for professional copywriter

I'd like a business card design that I can use to have my cards printed out by quillprint.com as a squared corners business card (see artwork and design guidelines here: https://help.quillprint.com/hc/en-gb/sections/200570950-QUILL-Product-Templates)

The design should be clean and modern and reflect the colours, tone and branding on my website: https://tessavorrin.com.au

Target Market(s)

Professionals, B2B small business owners

Industry/Entity Type

Business

Contact Information for Business Card

Tessa Vorrin
m: 0468 905 327
e: tessa@tessavorrin.com.au
w: tessavorrin.com.au

Font styles to use
Sans Serif

Requirements
Must have
• Tagline: "Smart copywriting for clever business people"
• Brand colours: fd8000, 009984, 666666 and black
Nice to have

```html
<!DOCTYPE html>
<html lang="en">
<head>
<meta charset="utf-8">
<title>Tessa Vorrin – Business Cards</title>
<link rel="stylesheet" href="https://fonts.googleapis.com/css2?family=Open+Sans:wght@400;600&display=swap">
<style>
  :root {
    --teal: #169a85;
    --orange: #f5821f;
    --grey: #666666;
    --white: #ffffff;
    --backdrop: #eceae7;
  }
  * { box-sizing: border-box; margin: 0; padding: 0; }
  html, body {
    width: 1200px; height: 900px; overflow: hidden;
    background: var(--backdrop);
    font-family: "Open Sans", Arial, sans-serif;
  }
  .canvas { position: relative; width: 1200px; height: 900px; }
  .card {
    position: absolute;
    overflow: hidden;
    box-shadow: 0 6px 18px rgba(0,0,0,0.18);
  }
  /* Front */
  .card--front { left: 78px; top: 33px; width: 590px; height: 365px; background: var(--white); }
  .card__bands { position: absolute; inset: 0; }
  .brand-name {
    position: absolute; left: 0; right: 0; top: 92px;
    display: flex; align-items: center; justify-content: center; gap: 14px;
  }
  .brand-name__dot { width: 18px; height: 18px; border-radius: 50%; background: var(--orange); }
  .brand-name__text { font-size: 46px; font-weight: 600; color: var(--teal); letter-spacing: -0.5px; line-height: 1; }
  .holder {
    position: absolute; left: 126px; top: 283px;
    color: var(--white); font-size: 20px; font-weight: 400; letter-spacing: 0.5px;
  }
  .divider { position: absolute; left: 295px; top: 266px; width: 1.5px; height: 59px; background: var(--white); }
  .contact-list { position: absolute; left: 309px; top: 264px; list-style: none; }
  .contact-list li {
    display: flex; align-items: center; gap: 9px;
    color: var(--white); font-size: 15px; line-height: 21.5px;
  }
  .contact-list svg { width: 13px; height: 13px; flex: none; }
  /* Back */
  .card--back { left: 388px; top: 505px; width: 567px; height: 352px; }
  .card__pattern { position: absolute; inset: 0; background: var(--teal); }
  .back-name {
    position: absolute; left: 0; right: 0; top: 155px;
    text-align: center; font-size: 48px; font-weight: 600; color: var(--white); line-height: 1;
  }
  .tagline {
    position: absolute; left: 0; right: 0; top: 283px;
    text-align: center; font-size: 16px; color: var(--white); letter-spacing: 1px; text-transform: uppercase;
  }
</style>
</head>
<body>
<main class="canvas">
  <section class="card card--front" aria-label="Business card front">
    <svg class="card__bands" width="590" height="365" viewBox="0 0 590 365" aria-hidden="true">
      <polygon points="0,200 402,200 382,226 0,226" fill="var(--orange)"/>
      <polygon points="0,230 386,230 414,192 590,192 590,365 0,365" fill="var(--teal)"/>
    </svg>
    <div class="brand-name">
      <span class="brand-name__dot"></span>
      <span class="brand-name__text">Tessa Vorrin</span>
    </div>
    <p class="holder">TESSA VORRIN</p>
    <span class="divider"></span>
    <ul class="contact-list">
      <li>
        <svg viewBox="0 0 13 13" aria-hidden="true"><rect x="3" y="0.5" width="7" height="12" rx="1.2" fill="none" stroke="#fff" stroke-width="1.3"/><circle cx="6.5" cy="10.3" r="0.8" fill="#fff"/></svg>
        0468 905 327
      </li>
      <li>
        <svg viewBox="0 0 13 13" aria-hidden="true"><rect x="0.5" y="2.5" width="12" height="8" fill="#fff"/><polyline points="0.8,3 6.5,7.2 12.2,3" fill="none" stroke="var(--teal)" stroke-width="1"/></svg>
        tessa@tessavorrin.com.au
      </li>
      <li>
        <svg viewBox="0 0 13 13" aria-hidden="true"><circle cx="6.5" cy="6.5" r="5.8" fill="#fff"/><path d="M4 3.5c1.5 0 2 1 1.5 2s-1.8.8-1.5 2.3M8.5 9.5c.3-1.3 1.5-1.2 2-2.3" fill="none" stroke="var(--teal)" stroke-width="1"/></svg>
        tessavorrin.com.au
      </li>
    </ul>
  </section>

  <section class="card card--back" aria-label="Business card back">
    <div class="card__pattern" role="img" aria-label="Repeating brand pattern in soft teal tones"></div>
    <p class="back-name">Tessa Vorrin</p>
    <p class="tagline">Smart copywriting for clever business people</p>
  </section>
</main>
</body>
</html>
```